ORV Web Design Project

I'm looking for a small, friendly,functional, information based website. If you go through the attachments, you would know the nature of the business.
Updates

Hi,

I have uploaded a picture of the CEO, Mr. Delvan Kroth PLMAT member. Please feel free to use it whereever appropriate.

Thanks!

Hello, I have uploaded some references. I like the colours used on the bar and would w

Example of a we page . I like this layout for the inside pages.

I am changing the tabs on my website to:

Home
About us
Services
Contact us

The services tab will have three sub pages:

Immigration
Education
AccommodationAccommodation

Target Market(s)

Young international students willing to come to Canada to study, young international students willing to immigrate to Canada, parents of the students

Industry/Entity Type

Business

Requirements
Must have
• ORV HOME
ABOUT US
CONTACT
SERVICES
TAG LINE

The website should look n feel trendy, smart, current, factual, trustworthy etc....
Nice to have
• I am looking for a bold, attractive, eye catchy home page with less text! Something that makes a statement....
Should not have
• No Clip art, flash animation, no bells n whistles please

```html
<!DOCTYPE html>
<html lang="en">
<head>
<meta charset="utf-8">
<title>ORV – Education</title>
<link rel="stylesheet" href="https://fonts.googleapis.com/css2?family=Questrial&family=Fredoka:wght@500;600&family=Dancing+Script:wght@400;600&display=swap">
<style>
:root{
  --dark:#333333;
  --red:#e31b23;
  --grey:#555555;
  --line:#d4d4d4;
  --white:#ffffff;
  --text:#222222;
}
*{margin:0;padding:0;box-sizing:border-box}
html,body{width:1200px;height:1058px;overflow:hidden;background:var(--white)}
body{position:relative;font-family:"Questrial",sans-serif;color:var(--text)}
.brand{position:absolute;left:0;top:0;width:326px;height:135px}
.brand-name{position:absolute;left:46px;top:40px;font-family:"Questrial",sans-serif;font-size:54px;line-height:1;color:var(--dark);letter-spacing:1px}
.brand-mark{position:absolute;left:170px;top:48px;width:22px;height:22px;background:var(--red)}
.brand-tag{position:absolute;left:46px;top:104px;font-family:"Dancing Script",cursive;font-size:18px;color:var(--dark)}
.nav{position:absolute;left:326px;top:0;width:874px;height:135px;background:var(--dark);display:flex;padding:24px 0 0 15px}
.nav a{font-family:"Fredoka",sans-serif;font-weight:600;font-size:20px;color:var(--white);text-decoration:none;height:84px;line-height:80px;padding:0 21px;border-right:1px solid #555}
.nav a:last-child{border-right:none}
.nav a.active{color:var(--red)}
.hero{position:absolute;left:238px;top:135px;width:962px;height:282px;background:linear-gradient(90deg,#8e4a34,#a65a3e 55%,#b86a4c)}
.hero-photo{position:absolute;right:100px;top:8px;width:200px;height:274px;background:linear-gradient(180deg,#3a2a24,#c8a690 45%,#f2f0ec)}
.hero-title{position:absolute;left:74px;top:108px;color:var(--white);font-family:"Fredoka",sans-serif;font-weight:600;line-height:1}
.hero-title .big{font-size:54px}
.hero-title .sub{font-size:36px;margin-top:4px;letter-spacing:.5px}
.statement{position:absolute;left:47px;top:190px;font-size:25px;line-height:24px;color:#111}
.statement .red{color:var(--red)}
.statement .lg{font-size:34px;line-height:33px;color:var(--grey)}
.statement .xl{font-size:40px;line-height:36px;color:var(--grey)}
.statement .ph{font-size:31px;line-height:34px;color:var(--red)}
.mission{position:absolute;left:0;top:418px;width:237px;height:180px;background:var(--dark);padding:22px 0 0 47px;color:var(--white);font-size:15px;line-height:18px}
.mission h2{font-family:"Dancing Script",cursive;font-weight:400;color:var(--red);font-size:20px;margin-bottom:2px}
.values{position:absolute;left:47px;top:626px;width:180px}
.values h3{font-size:16px;line-height:18px;color:var(--grey);font-weight:700}
.values ul{list-style:none;margin-top:8px}
.values li{font-size:15px;line-height:20px;color:#777;padding-left:16px;position:relative}
.values li::before,.reasons li::before{content:"";position:absolute;left:0;top:7px;width:6px;height:6px;background:var(--red)}
.motto{position:absolute;left:47px;top:774px;font-family:"Dancing Script",cursive;font-size:22px;line-height:30px;color:#111}
.motto .accent{color:var(--red);font-size:34px}
.divider-v{position:absolute;left:237px;top:417px;width:2px;height:524px;background:var(--line)}
.divider-h1{position:absolute;left:0;top:417px;width:238px;height:2px;background:var(--line)}
.divider-h2{position:absolute;left:0;top:598px;width:238px;height:2px;background:var(--line)}
.content{position:absolute;left:310px;top:457px;width:650px}
.content p{font-size:12.5px;line-height:18px;text-align:justify}
.content h4{font-weight:400;color:var(--red);font-size:15px;margin:17px 0 22px}
.reasons{list-style:none}
.reasons li{font-size:12.5px;line-height:16px;padding-left:14px;position:relative;margin-bottom:20px}
.reasons li::before{top:5px}
.footer{position:absolute;left:0;top:941px;width:1200px;height:117px;border-top:2px solid var(--line)}
.badge{position:absolute;left:45px;top:18px;width:155px;height:72px}
.copy{position:absolute;left:0;width:1200px;top:50px;text-align:center;font-size:11px;font-weight:700}
.social{position:absolute;right:56px;top:40px;display:flex;gap:6px}
.social span{width:27px;height:27px;border-radius:50%;background:var(--dark)}
.social span:first-child{background:#b3141b}
</style>
</head>
<body>
<header class="brand">
  <div class="brand-name">ORV</div>
  <div class="brand-mark"></div>
  <div class="brand-tag">Your Canada Specialist</div>
</header>
<nav class="nav">
  <a href="#">Home</a><a href="#">About Us</a><a href="#">Immigration</a><a href="#" class="active">Education</a><a href="#">Accommodation</a><a href="#">Contact Us</a>
</nav>
<section class="hero">
  <div class="hero-photo" role="img" aria-label="Smiling student holding notebooks in front of a brick wall"></div>
  <div class="hero-title"><div class="big">education</div><div class="sub">ORION RIDGE VENTURES</div></div>
</section>
<div class="statement">At <span class="red">ORV</span> we are<br>Committed<br>to our<br><span class="lg">Customer</span><br><span class="xl">Centred</span><br><span class="ph">Philosophy</span></div>
<div class="divider-h1"></div>
<aside class="mission"><h2>Our Mission</h2>Is to help our clients<br>achieve their goals<br>by providing them<br>with world class<br>customer service that is<br>Reliable and Superior</aside>
<div class="divider-h2"></div>
<div class="values"><h3>WE ARE DRIVEN<br>BY OUR CORE VALUES:</h3><ul><li>Ethics</li><li>Expertise</li><li>Leadership</li></ul></div>
<div class="motto">We have been<br><span class="accent" style="padding-left:46px">there</span><br><span style="padding-left:8px">We know what it</span><br><span class="accent" style="padding-left:90px">takes</span></div>
<div class="divider-v"></div>
<main class="content">
  <p>Canada has one of the best education systems in the world. Canada spends more on education (per capita) than any other G-8 country. Every year thousands of students from all over the world pursue their educational goals in Canada. ORV prides itself on emerging as one of the key stakeholders in Canadian education which has been possible due to its principals working tirelessly and guiding every student as they would someone from their own family member and we look forward to working with you to meet your individual needs.</p>
  <h4>Read on to find out why Canada is the number one choice for students from all over the world?</h4>
  <ul class="reasons">
    <li>Canadian credentials recognized and respected around the globe</li>
    <li>Affordable education</li>
    <li>Possibility of Immigration after graduation</li>
    <li>Work opportunities after completion of studies</li>
    <li>One of the safest countries to live and ranked as one the best countries to live, year after year</li>
    <li>World class institutes</li>
    <li>State of the art Campus facilities</li>
    <li>Practical and Hands-on education</li>
  </ul>
</main>
<footer class="footer">
  <svg class="badge" viewBox="0 0 155 72" role="img" aria-label="Regulatory council membership badge">
    <circle cx="36" cy="36" r="34" fill="#3b82c4"/>
    <rect x="80" y="10" width="75" height="52" rx="4" fill="#2a3a5c"/>
  </svg>
  <div class="copy">© 2013 orvcanada.com. All rights reserved.</div>
  <div class="social"><span></span><span></span><span></span><span></span></div>
</footer>
</body>
</html>
```